New Business Card Design Project

We require a business card design for Vexalund, a newly established Indian company.
Our focus is on the development, manufacturing, and export of a diverse array of pharmaceutical products on a global scale. The card should convey a professional appearance, as our primary markets are in Africa, China, and Southeast Asian nations.
We envision a two-sided business card, with the reverse side dedicated to a logo set against a solid color or an elegantly designed pattern. The corners should be rounded. We would appreciate seeing both horizontal and vertical design options. We trust the designer to utilize their expertise in creating this design.

The content for the business card is included in the attached Word file.

Target Market(s)

Our primary markets are in Africa, China, and Southeast Asian, Latin America, Maldives, Sri Lanka

Industry/Entity Type

Pharmaceutical Manufacturing and Export

Contact Information for Business Card

Colors

Designer to choose colors to be used in the design.

Requirements
Must have
• The reverse side of the business card features solely the logo along with the tagline, "Cures for Living."
Should not have
• The logo should not exceed two instances, encompassing both the front and back sides of the card.

```html
<!DOCTYPE html>
<html lang="en">
<head>
<meta charset="utf-8">
<title>Vexalund Business Card</title>
<link rel="stylesheet" href="https://fonts.googleapis.com/css2?family=Montserrat:wght@500;700&family=Open+Sans:wght@400;700&display=swap">
<style>
  :root {
    --stage: #232323;
    --card: #1c1c1c;
    --blue: #2ba6e0;
    --coral: #f0614d;
    --white: #f2f2f2;
    --band-gap: #111111;
    --shadow: rgba(0,0,0,0.55);
  }
  * { margin: 0; padding: 0; box-sizing: border-box; }
  html, body { width: 1200px; height: 711px; overflow: hidden; background: var(--stage); }
  .stage { position: relative; width: 1200px; height: 711px; }
  .card {
    position: absolute; width: 520px; height: 300px; top: 206px;
    background: var(--card); border-radius: 22px; overflow: hidden;
    box-shadow: 0 14px 30px var(--shadow);
  }
  .card--back { left: 45px; }
  .card--front { left: 635px; }
  .card__bands { position: absolute; inset: 0; width: 100%; height: 100%; }
  .brand {
    position: absolute; display: flex; align-items: center; gap: 10px;
    font-family: "Montserrat", sans-serif; font-weight: 700; color: var(--blue);
    white-space: nowrap;
  }
  .brand__dot { width: 14px; height: 14px; border-radius: 50%; background: var(--coral); }
  .card--back .brand { left: 0; right: 0; top: 100px; justify-content: center; font-size: 50px; }
  .tagline {
    position: absolute; left: 0; right: 0; top: 170px; text-align: center;
    font-family: "Montserrat", sans-serif; font-weight: 500; font-size: 13px;
    color: var(--blue); letter-spacing: 0.5px;
  }
  .card--front .brand { left: 28px; top: 118px; font-size: 36px; }
  .card--front .brand__dot { width: 11px; height: 11px; }
  .divider {
    position: absolute; left: 258px; top: 40px; width: 1px; height: 165px;
    background: var(--coral); transform: rotate(-18deg); transform-origin: top;
  }
  .contact { position: absolute; left: 318px; top: 52px; font-family: "Open Sans", sans-serif; }
  .contact__name { font-size: 20px; color: var(--blue); font-weight: 400; white-space: nowrap; }
  .contact__name strong { font-weight: 700; }
  .contact__role { font-size: 13px; color: var(--white); margin-top: 1px; }
  .contact__list { list-style: none; margin-top: 16px; }
  .contact__item {
    display: flex; align-items: center; gap: 8px;
    font-size: 12px; color: var(--white); line-height: 20px; white-space: nowrap;
  }
  .contact__icon { width: 13px; height: 13px; flex: none; }
  .address {
    position: absolute; right: 30px; top: 222px; white-space: nowrap;
    font-family: "Open Sans", sans-serif; font-size: 12.5px; color: var(--blue);
  }
</style>
</head>
<body>
<main class="stage">

  <section class="card card--back" aria-label="Card reverse">
    <svg class="card__bands" viewBox="0 0 520 300" aria-hidden="true">
      <polygon points="0,300 0,292 280,266 330,266 330,300" fill="var(--blue)"/>
      <polygon points="305,262 520,232 520,300 330,300 330,266" fill="var(--coral)"/>
      <polygon points="305,262 330,266 330,300 322,300" fill="var(--band-gap)"/>
    </svg>
    <div class="brand"><span class="brand__dot"></span>Vexalund</div>
    <p class="tagline">Cures for Living.</p>
  </section>

  <section class="card card--front" aria-label="Card front">
    <svg class="card__bands" viewBox="0 0 520 300" aria-hidden="true">
      <polygon points="0,300 0,292 280,266 330,266 330,300" fill="var(--blue)"/>
      <polygon points="305,262 520,232 520,300 330,300 330,266" fill="var(--coral)"/>
      <polygon points="305,262 330,266 330,300 322,300" fill="var(--band-gap)"/>
    </svg>
    <div class="brand"><span class="brand__dot"></span>Vexalund</div>
    <span class="divider" aria-hidden="true"></span>
    <div class="contact">
      <h1 class="contact__name"><strong>Ravindra</strong> K. Sathe</h1>
      <p class="contact__role">CEO</p>
      <ul class="contact__list">
        <li class="contact__item">
          <svg class="contact__icon" viewBox="0 0 14 14" aria-hidden="true"><rect x="3" y="1" width="8" height="12" rx="1.5" fill="none" stroke="var(--coral)" stroke-width="1.5"/></svg>
          +91 90210 55318
        </li>
        <li class="contact__item">
          <svg class="contact__icon" viewBox="0 0 14 14" aria-hidden="true"><circle cx="7" cy="7" r="6" fill="var(--blue)"/><path d="M1 7h12M7 1c-3 3-3 9 0 12M7 1c3 3 3 9 0 12" fill="none" stroke="var(--card)" stroke-width="0.9"/></svg>
          www.vexalund.com
        </li>
        <li class="contact__item">
          <svg class="contact__icon" viewBox="0 0 14 14" aria-hidden="true"><rect x="1" y="3" width="12" height="9" fill="var(--coral)"/><path d="M1 3l6 5 6-5" fill="none" stroke="var(--card)" stroke-width="1"/></svg>
          rsathe@vexalund.com
        </li>
      </ul>
    </div>
    <p class="address">14, Kamal Nagar, Wardha, 442001, India</p>
  </section>

</main>
</body>
</html>
```